Business Card: RW Office Partners - Your organised problem solver

Business Name: RW Office Partners
Website: www.rwofficepartners.com.au
Email: marisol@rwofficepartners.com.au
Mobile: 61 482 907 236
Facebook: @rwofficepartners
Instrgram: @rwofficepartners

Brading Colours:
HEX
#986474
#ddccd3
#7a8498
#c9d8e4
#000000
#ffffff

Tag Line: Calm support for busy offices

Link to DRAFT website:
https://deskhelpcollective.wixsite.com/rw-office-partners

About Page from the website:
My name is Marisol Wrenfield, and I would love to assist you to become more productive in your day to day and achieve your business and personal goals.
My mission is to give you time, time to work on the important tasks of your business or to be able to spend more time with your family. I will take on the tasks you don’t have time for, don’t know well or simply don’t like to do.
I have an extensive background in Administration, Tender Coordination, Document Control, WHS and Quality Management working primarily in the Construction, Mining and Corporate World.
I am passionate about being organised, having order and making things in your life (and mine) easier! I love to watch something unfold and grow into something amazing! I am known for being the go-to problem solver, the organiser of all things, producing high standards of work even under pressure. I’m also a confident communicator, and I understand that you’re busy running your business.

Target Market(s)

Small to Medium Business who require assistance in their business by a virtual assistant.

Industry/Entity Type

Virtual Assistant

Contact Information for Business Card

Mobile: 61 482 907 236

Font styles to use
Sans Serif

Colors
ffffff

Requirements
Must have
• Branding Colours as outlined.
Contact Details as outlined.
Logo as provided.
Proper contact details - mobile, facebook, instragm, website.
Simple, Elegant, very clean looking.
Should not have
• Note cute with pictures.
Not too girly as still want to market to construction companies.

```html
<!DOCTYPE html>
<html lang="en">
<head>
<meta charset="utf-8">
<title>RW Office Partners – Business Card</title>
<link rel="stylesheet" href="https://fonts.googleapis.com/css2?family=Montserrat:wght@500;600&family=Roboto:wght@400;500&display=swap">
<style>
  :root {
    --stage: #3a3a3c;
    --card: #262427;
    --mauve: #986474;
    --blush: #ddccd3;
    --slate: #7a8498;
    --mist: #c9d8e4;
    --white: #ffffff;
  }
  * { box-sizing: border-box; margin: 0; padding: 0; }
  html, body { width: 799px; height: 1200px; overflow: hidden; }
  body {
    background: var(--stage);
    font-family: "Roboto", Arial, sans-serif;
    position: relative;
  }
  .card {
    position: absolute;
    left: 60px;
    width: 680px;
    height: 388px;
    background: var(--card);
    border-radius: 4px;
    overflow: hidden;
    box-shadow: 0 14px 30px rgba(0,0,0,.45);
  }
  .card--front { top: 150px; }
  .card--back { top: 662px; }

  .wordmark {
    font-family: "Montserrat", Arial, sans-serif;
    font-weight: 600;
    color: var(--mauve);
    letter-spacing: .02em;
    white-space: nowrap;
  }
  .card--front .wordmark {
    position: absolute;
    top: 118px;
    left: 0; right: 0;
    text-align: center;
    font-size: 46px;
  }
  .social-row {
    position: absolute;
    top: 250px;
    left: 0; right: 0;
    display: flex;
    justify-content: center;
    gap: 26px;
    color: var(--white);
    font-size: 17px;
  }
  .social-item { display: flex; align-items: center; gap: 8px; }
  .mark-square {
    width: 12px; height: 12px;
    border-radius: 2px;
    background: var(--mauve);
    flex: none;
  }

  .card--back .wordmark {
    position: absolute;
    top: 92px;
    left: 44px;
    font-size: 30px;
  }
  .contact-block {
    position: absolute;
    top: 140px;
    left: 360px;
    color: var(--white);
  }
  .person-name {
    font-family: "Montserrat", Arial, sans-serif;
    font-weight: 600;
    font-size: 19px;
    color: var(--mauve);
  }
  .person-role { font-size: 14px; margin-top: 3px; margin-bottom: 10px; }
  .contact-list { list-style: none; font-size: 14px; }
  .contact-list li {
    display: flex; align-items: center; gap: 10px;
    height: 21px;
  }
  .contact-list svg { width: 12px; height: 12px; flex: none; }

  .accent-band {
    position: absolute;
    left: 0;
    top: 300px;
    width: 300px;
    height: 16px;
    background: var(--slate);
  }
  .tagline-tab {
    position: absolute;
    left: 296px;
    right: 0;
    bottom: 0;
    height: 72px;
    background: var(--mauve);
    border-top-left-radius: 26px;
    color: var(--white);
    font-size: 16px;
    display: flex;
    align-items: center;
    padding-left: 44px;
  }
</style>
</head>
<body>

<section class="card card--front" aria-label="Card front">
  <div class="wordmark">RW Office Partners</div>
  <div class="social-row">
    <span class="social-item"><span class="mark-square"></span>@rwofficepartners</span>
    <span class="social-item"><span class="mark-square"></span>@rwofficepartners</span>
  </div>
</section>

<section class="card card--back" aria-label="Card back">
  <div class="wordmark">RW Office Partners</div>

  <div class="contact-block">
    <div class="person-name">Marisol Wrenfield</div>
    <div class="person-role">Virtual Assistant</div>
    <ul class="contact-list">
      <li>
        <svg viewBox="0 0 12 12" aria-hidden="true"><path d="M2.5 1h2l1 3-1.3.9a7 7 0 0 0 2.9 2.9L8 6.5l3 1v2a1.5 1.5 0 0 1-1.5 1.5A8.5 8.5 0 0 1 1 2.5 1.5 1.5 0 0 1 2.5 1z" fill="var(--mauve)"/></svg>
        61 482 907 236
      </li>
      <li>
        <svg viewBox="0 0 12 12" aria-hidden="true"><rect x="1" y="2.5" width="10" height="7" rx="1" fill="var(--mauve)"/><path d="M1.5 3l4.5 3.5L10.5 3" stroke="var(--card)" stroke-width="1" fill="none"/></svg>
        marisol@rwofficepartners.com.au
      </li>
      <li>
        <svg viewBox="0 0 12 12" aria-hidden="true"><circle cx="6" cy="6" r="5" fill="none" stroke="var(--mauve)" stroke-width="1.4"/><path d="M1 6h10M6 1c2.5 3 2.5 7 0 10M6 1c-2.5 3-2.5 7 0 10" stroke="var(--mauve)" stroke-width="1" fill="none"/></svg>
        www.rwofficepartners.com.au
      </li>
      <li><span class="mark-square"></span>@rwofficepartners</li>
      <li><span class="mark-square"></span>@rwofficepartners</li>
    </ul>
  </div>

  <div class="accent-band"></div>
  <div class="tagline-tab">Calm support for busy offices</div>
</section>

</body>
</html>
```